Create an awesome website for a medical clinic

This is a new website for a doctor's office. The site should be clean and modern, easy to navigate.

This is a wellness clinic, we want to help our clients have a healthy, active lifestyle. It should be friendly and inviting, and easy for them to call or schedule an appointment.

The site should be responsive and designed using the attached Bootstrap 3 PSD.

We will provide stock photos, until then please use stock photos from:

pixelharbor.com or
framequarry.com (preferred)

Some example sites of clean and modern designs that we like:

https://tulsaspinecare.com/
http://reachpastjoints.com/
http://turninghealthier.com/

Also attached is a temporary logo you can use.

Reason: Thank you everyone for your great designs - we need a little more time so I'm extending the project.

Need extra days to review

Also, the colors in the new logo I just linked to are the final colors of the logo, so feel free to use any complimentary colors to it.

Hi everyone, The boss wants to change the layout of the site a little bit - here's the revised layout: https://www.filecrate.com/s/k9rt31vx2qp84zn/notes%2011_29_2017.pdf?dl=0 And the graphic assets you can use are here: https://www.filecrate.com/s/k9rt31vx2qp84zn/notes%2011_29_2017.pdf?dl=0 Feel free to change the background color of the "topbar", and change the icons of the "why people trust us" if you want, these are just temporary placeholders. Thanks for your patience and hard work!

Target Market(s)

People seeking medical treatment (wellness clinic)

Industry/Entity Type

Doctor

Number of Pages Required

1 page

Font styles to use
Sans Serif

Colors
0592cd
33a6d7
abd037
9bcb3c

Requirements
Must have
• The home page should have: a strong hero image/slideshow, clinic phone number should be prominent and at the top of the page (in the nav), a "what to expect" section (this is like a FAQs section - see attachment), and a strong call to action (a button to call or schedule an appointment).
• The what to expect section is useful so that prospective clients can determine if we're a good fit for them or not. It's a basic, first-step pre-qualification block of information.
• Social media icons which links to our social media profiles should be included.
Nice to have
• - Link to 3 most recent blog entries
• - Testimonials
• - How a multilevel nav menu looks.

```html
<!DOCTYPE html>
<html lang="en">
<head>
<meta charset="utf-8">
<title>Wellness Clinic</title>
<link href="https://fonts.googleapis.com/css2?family=Roboto:wght@300;400;500;700&display=swap" rel="stylesheet">
<style>
:root{
  --blue:#33a6d7;
  --blue-dark:#0592cd;
  --green:#9bcb3c;
  --card:#f3f3f4;
  --title:#8a8a8a;
  --text:#b4b4b4;
  --footer:#6b6f77;
  --footer-dark:#5d6168;
  --white:#ffffff;
}
*{box-sizing:border-box;margin:0;padding:0}
html,body{width:1200px;height:3259px;overflow:hidden}
body{font-family:'Roboto',sans-serif;background:var(--white);color:var(--text);position:relative}
.section-title{font-weight:400;font-size:19px;letter-spacing:.5px;color:var(--title);text-align:center;text-transform:uppercase}
.section-arrow{display:block;margin:14px auto 0}

/* Advantages */
.advantages{position:absolute;top:0;left:0;width:1200px;height:726px}
.advantages .section-title{position:absolute;top:92px;width:100%}
.advantages .section-arrow{position:absolute;top:140px;left:588px}
.adv-grid{position:absolute;top:236px;left:98px;display:grid;grid-template-columns:repeat(3,317px);grid-template-rows:repeat(2,183px);column-gap:26px;row-gap:29px}
.adv-card{background:var(--card);display:flex;flex-direction:column;align-items:center;padding-top:36px}
.adv-card p{margin-top:16px;font-size:14px;line-height:23px;text-align:center;color:var(--text);font-weight:300}

/* Testimonials */
.testimonials{position:absolute;top:726px;left:0;width:1200px;height:492px}
.testimonial-photo{position:absolute;inset:0;background:linear-gradient(90deg,#b9b3ab 0%,#cfc9c2 25%,#a9b6c2 55%,#8ea0b6 75%,#b7bfa9 100%)}
.testimonial-overlay{position:absolute;inset:0;background:rgba(70,74,82,.45)}
.testimonials .section-title{position:absolute;top:93px;width:100%;color:var(--white)}
.testimonials .section-arrow{position:absolute;top:142px;left:588px}
.quote-mark{position:absolute;top:226px}
.quote-text{position:absolute;top:233px;left:310px;width:580px;text-align:center;color:var(--white);font-size:14px;line-height:23px;font-weight:300}
.quote-author{position:absolute;top:320px;width:100%;text-align:center;color:var(--white);font-size:14px;font-weight:300}
.quote-author b{font-weight:500}
.slider-dots{position:absolute;top:372px;left:572px;display:flex;gap:8px}
.slider-dots span{width:22px;height:22px;border:1px solid rgba(255,255,255,.7)}

/* Blog */
.blog{position:absolute;top:1218px;left:0;width:1200px;height:666px}
.blog .section-title{position:absolute;top:93px;width:100%}
.blog .section-arrow{position:absolute;top:142px;left:588px}
.blog-grid{position:absolute;top:236px;left:98px;display:grid;grid-template-columns:repeat(3,317px);column-gap:26px}
.post{background:var(--white);height:334px;box-shadow:0 2px 10px rgba(0,0,0,.12)}
.post-image{height:142px}
.post-image.one{background:linear-gradient(120deg,#dfe3e6,#c9ced2 50%,#eef0f1)}
.post-image.two{background:linear-gradient(120deg,#9cc1cc,#d9cfc6 55%,#b8c2c6)}
.post-image.three{background:linear-gradient(120deg,#e8e2da,#c9b7a6 50%,#dfe6df)}
.post-body{padding:32px 26px 0}
.post-title{font-size:15px;font-weight:400;color:#666}
.post-text{margin-top:10px;font-size:11.5px;line-height:16px;color:var(--text);font-weight:300}
.post-more{display:inline-flex;align-items:center;gap:8px;margin-top:10px;font-size:11px;color:var(--blue);text-decoration:none}

/* Contact */
.contact{position:absolute;top:1884px;left:0;width:1200px;height:586px;background:linear-gradient(90deg,#8b8f95 0%,#b7b9bb 35%,#a3a6aa 65%,#7f8389 100%)}
.contact-figure{position:absolute;left:120px;top:100px;width:540px;height:486px;background:linear-gradient(180deg,#e6e4e2,#d8dde3 60%,#c9d2dc)}
.contact-form{position:absolute;left:726px;top:79px;width:316px;height:426px;background:var(--white);padding:40px 35px 0}
.contact-form h3{font-size:18px;font-weight:400;color:#888;text-align:center}
.field{display:block;width:100%;height:30px;margin-top:14px;border:1px solid #e3e3e3;font-size:10px;color:#aaa;padding:9px 7px;font-family:inherit}
.contact-form h3+.field{margin-top:24px}
.field.message{height:105px}
.send-btn{display:block;width:100%;height:29px;margin-top:11px;background:var(--blue);color:var(--white);border:0;font-size:10.5px;font-family:inherit}

/* Footer */
.site-footer{position:absolute;top:2470px;left:0;width:1200px;height:389px;background:var(--footer);color:#e6e7e9}
.socials{position:absolute;top:42px;left:98px;display:flex;gap:10px}
.socials span{width:32px;height:32px;border:1px solid #e6e7e9;border-radius:50%}
.info{position:absolute;top:40px;display:flex;gap:14px;align-items:center}
.info-icon{width:34px;height:34px;border-radius:50%;display:flex;align-items:center;justify-content:center}
.info-icon.blue{background:var(--blue)}
.info-icon.green{background:var(--green)}
.info strong{display:block;font-size:13px;font-weight:500;color:var(--white)}
.info small{display:block;font-size:11px;margin-top:3px;color:#e0e1e3}
.col{position:absolute;top:154px}
.col h4{font-size:13px;font-weight:400;color:var(--white);margin-bottom:12px}
.col p,.col li{font-size:11px;line-height:21px;color:#e3e4e6;list-style:none;font-weight:300}
.col.about p{line-height:17px;width:200px}
.hours{width:232px}
.hours li{display:flex;justify-content:space-between}
.hours li span:last-child{font-size:10px}
.hours li.today{font-weight:700;color:var(--white)}

/* Map */
.map{position:absolute;top:2859px;left:0;width:1200px;height:350px;background:linear-gradient(180deg,#f1f1f1,#e6e6e6 50%,#eeeeee)}
.map-pin{position:absolute;top:154px;left:580px}
.bottom-bar{position:absolute;top:3209px;left:0;width:1200px;height:50px;background:var(--footer-dark)}
.to-top{position:absolute;top:3169px;left:560px;width:80px;height:40px;background:var(--footer-dark);border-radius:40px 40px 0 0;display:flex;justify-content:center;padding-top:12px}
</style>
</head>
<body>

<section class="advantages">
  <h2 class="section-title">Our Advantages</h2>
  <svg class="section-arrow" width="24" height="28" viewBox="0 0 24 28"><path d="M12 2v23M3 16l9 9 9-9" fill="none" stroke="#33a6d7" stroke-width="1.6"/></svg>
  <div class="adv-grid">
    <div class="adv-card">
      <svg width="46" height="34" viewBox="0 0 46 34"><path d="M3 8h24v18H3zM27 13h9l7 7v6H27z" fill="#33a6d7"/><circle cx="11" cy="28" r="4" fill="#33a6d7" stroke="#f3f3f4" stroke-width="2"/><circle cx="35" cy="28" r="4" fill="#33a6d7" stroke="#f3f3f4" stroke-width="2"/><path d="M13 12h4v4h4v4h-4v4h-4v-4H9v-4h4z" fill="#fff"/></svg>
      <p>Lorem ipsum dolor set amet<br>adipiscing</p>
    </div>
    <div class="adv-card">
      <svg width="44" height="36" viewBox="0 0 44 36"><path d="M15 8V3h14v5" fill="none" stroke="#33a6d7" stroke-width="3"/><rect x="2" y="8" width="40" height="26" rx="4" fill="#33a6d7"/><path d="M19 13h6v5h5v6h-5v5h-6v-5h-5v-6h5z" fill="#fff"/></svg>
      <p>Lorem ipsum dolor set amet<br>adipiscing</p>
    </div>
    <div class="adv-card">
      <svg width="40" height="40" viewBox="0 0 40 40"><rect x="13" y="-2" width="14" height="44" rx="7" transform="rotate(45 20 20)" fill="#33a6d7"/><rect x="13" y="-2" width="14" height="44" rx="7" transform="rotate(-45 20 20)" fill="#33a6d7"/><circle cx="20" cy="20" r="5" fill="#fff"/></svg>
      <p>Lorem ipsum dolor set amet<br>adipiscing</p>
    </div>
    <div class="adv-card">
      <svg width="36" height="38" viewBox="0 0 36 38"><path d="M9 6c3-4 15-4 18 0v6H9z" fill="#33a6d7"/><circle cx="18" cy="15" r="7" fill="#33a6d7"/><path d="M3 37c0-10 6-15 15-15s15 5 15 15z" fill="#33a6d7"/><path d="M16 27h4v3h3v4h-3v3h-4v-3h-3v-4h3z" fill="#fff"/></svg>
      <p>Lorem ipsum dolor set amet<br>adipiscing</p>
    </div>
    <div class="adv-card">
      <svg width="50" height="36" viewBox="0 0 50 36"><g transform="rotate(25 25 18)"><rect x="4" y="10" width="42" height="16" rx="8" fill="none" stroke="#33a6d7" stroke-width="3"/><path d="M25 10h13a8 8 0 0 1 0 16H25z" fill="#33a6d7"/></g></svg>
      <p>Lorem ipsum dolor set amet<br>adipiscing</p>
    </div>
    <div class="adv-card">
      <svg width="36" height="40" viewBox="0 0 36 40"><path d="M6 3v12a8 8 0 0 0 16 0V3" fill="none" stroke="#33a6d7" stroke-width="3"/><path d="M14 23v6a7 7 0 0 0 14 0v-9" fill="none" stroke="#33a6d7" stroke-width="3"/><circle cx="28" cy="16" r="4" fill="none" stroke="#33a6d7" stroke-width="3"/></svg>
      <p>Lorem ipsum dolor set amet<br>adipiscing</p>
    </div>
  </div>
</section>

<section class="testimonials">
  <div class="testimonial-photo" role="img" aria-label="Photo of a smiling doctor with an older patient giving a thumbs up"></div>
  <div class="testimonial-overlay"></div>
  <h2 class="section-title">What Others Are Saying</h2>
  <svg class="section-arrow" width="24" height="28" viewBox="0 0 24 28"><path d="M12 2v23M3 16l9 9 9-9" fill="none" stroke="#fff" stroke-width="1.6"/></svg>
  <svg class="quote-mark" style="left:248px" width="36" height="30" viewBox="0 0 36 30"><path d="M2 28V17C2 8 7 3 15 2v5c-4 1-6 4-6 8h6v13zM20 28V17c0-9 5-14 13-15v5c-4 1-6 4-6 8h6v13z" fill="#fff"/></svg>
  <svg class="quote-mark" style="left:916px" width="36" height="30" viewBox="0 0 36 30"><path d="M34 2v11c0 9-5 14-13 15v-5c4-1 6-4 6-8h-6V2zM16 2v11c0 9-5 14-13 15v-5c4-1 6-4 6-8H3V2z" fill="#fff"/></svg>
  <p class="quote-text">Sed ut perspiciatis unde omnis iste natus error sit voluptatem accus adoloremque laudantium, totam rem aperiam, eaque ipsa quae ab illo inventore veritatis et quasi architecto beatae</p>
  <p class="quote-author"><b>Mira Stone,</b> sport trainer</p>
  <div class="slider-dots"><span></span><span></span></div>
</section>

<section class="blog">
  <h2 class="section-title">Latest News From Our Blog</h2>
  <svg class="section-arrow" width="24" height="28" viewBox="0 0 24 28"><path d="M12 2v23M3 16l9 9 9-9" fill="none" stroke="#33a6d7" stroke-width="1.6"/></svg>
  <div class="blog-grid">
    <article class="post">
      <div class="post-image one" role="img" aria-label="Photo of a doctor typing on a keyboard at a desk"></div>
      <div class="post-body">
        <h3 class="post-title">Lorem ipsum dolor set amet</h3>
        <p class="post-text">Sed ut perspiciatis unde omnis iste natus error sit voluptatem accusantium doloremque laudantium, totam rem aperiam, eaque ipsa quae ab illo inventore veritatis et quasi</p>
        <a class="post-more" href="#">MORE <svg width="6" height="9" viewBox="0 0 6 9"><path d="M1 1l3.5 3.5L1 8" fill="none" stroke="#33a6d7" stroke-width="1.3"/></svg></a>
      </div>
    </article>
    <article class="post">
      <div class="post-image two" role="img" aria-label="Photo of smiling medical staff in a clinic"></div>
      <div class="post-body">
        <h3 class="post-title">Lorem ipsum dolor set amet</h3>
        <p class="post-text">Sed ut perspiciatis unde omnis iste natus error sit voluptatem accusantium doloremque laudantium, totam rem aperiam, eaque ipsa quae ab illo inventore veritatis et quasi</p>
        <a class="post-more" href="#">MORE <svg width="6" height="9" viewBox="0 0 6 9"><path d="M1 1l3.5 3.5L1 8" fill="none" stroke="#33a6d7" stroke-width="1.3"/></svg></a>
      </div>
    </article>
    <article class="post">
      <div class="post-image three" role="img" aria-label="Photo of a doctor examining a young child"></div>
      <div class="post-body">
        <h3 class="post-title">Lorem ipsum dolor set amet</h3>
        <p class="post-text">Sed ut perspiciatis unde omnis iste natus error sit voluptatem accusantium doloremque laudantium, totam rem aperiam, eaque ipsa quae ab illo inventore veritatis et quasi</p>
        <a class="post-more" href="#">MORE <svg width="6" height="9" viewBox="0 0 6 9"><path d="M1 1l3.5 3.5L1 8" fill="none" stroke="#33a6d7" stroke-width="1.3"/></svg></a>
      </div>
    </article>
  </div>
</section>

<section class="contact">
  <div class="contact-figure" role="img" aria-label="Photo of a young doctor with a stethoscope pointing toward the contact form"></div>
  <form class="contact-form">
    <h3>Send us a Message</h3>
    <div class="field">Full Name</div>
    <div class="field">Phone number</div>
    <div class="field">Email Address</div>
    <div class="field message">Type your message</div>
    <button class="send-btn" type="button">Send Message</button>
  </form>
</section>

<footer class="site-footer">
  <div class="socials" aria-label="Social media links"><span></span><span></span><span></span></div>
  <div class="info" style="left:356px">
    <span class="info-icon blue"><svg width="12" height="16" viewBox="0 0 12 16"><path d="M6 15S1 9 1 6a5 5 0 0 1 10 0c0 3-5 9-5 9z" fill="#fff"/><circle cx="6" cy="6" r="2" fill="#33a6d7"/></svg></span>
    <div><strong>Our Address</strong><small>418 W Cedar Hollow Rd</small></div>
  </div>
  <div class="info" style="left:614px">
    <span class="info-icon green"><svg width="14" height="14" viewBox="0 0 14 14"><circle cx="7" cy="7" r="6" fill="#fff"/><path d="M7 3.5V7l2.5 1.5" fill="none" stroke="#9bcb3c" stroke-width="1.5"/></svg></span>
    <div><strong>Open Hours</strong><small>Mon - Friday: 8AM - 5PM</small></div>
  </div>
  <div class="info" style="left:870px">
    <span class="info-icon blue"><svg width="14" height="14" viewBox="0 0 14 14"><path d="M3 1l2.5 3-1.5 1.5a8 8 0 0 0 4.5 4.5L10 8.5l3 2.5-1.5 2C6 13 1 8 1 2.5z" fill="#fff"/></svg></span>
    <div><strong>Give us a Call</strong><small>+1(555) 014 - 2290</small></div>
  </div>

  <div class="col about" style="left:98px">
    <h4>About us</h4>
    <p>Sed ut perspiciatis unde omnis iste natus error sit voluptatem accu santium doloremque laudantium, totam rem veritatis et quasi</p>
  </div>
  <div class="col" style="left:356px">
    <h4>Navigation</h4>
    <ul><li>Home</li><li>About</li><li>Services</li><li>Blog</li><li>Contact us</li></ul>
  </div>
  <div class="col" style="left:614px">
    <h4>Services</h4>
    <ul><li>Lorem ipsum</li><li>Set amet</li><li>Dolor lorem</li><li>Omnis iste</li></ul>
  </div>
  <div class="col" style="left:870px">
    <h4>Working Hours</h4>
    <ul class="hours">
      <li><span>Monday</span><span>08:00 - 17:00</span></li>
      <li><span>Tuesday</span><span>08:00 - 17:00</span></li>
      <li><span>Wednesday</span><span>08:00 - 17:00</span></li>
      <li class="today"><span>Thursday</span><span>08:00 - 17:00</span></li>
      <li><span>Friday</span><span>08:00 - 17:00</span></li>
      <li><span>Saturday</span><span>10:00 - 16:00</span></li>
      <li><span>Sunday</span><span>Closed</span></li>
    </ul>
  </div>
</footer>

<div class="map" role="img" aria-label="Street map showing the clinic location"></div>
<svg class="map-pin" width="40" height="54" viewBox="0 0 40 54"><path d="M20 52S3 30 3 19a17 17 0 0 1 34 0c0 11-17 33-17 33z" fill="#33a6d7"/><circle cx="20" cy="19" r="6" fill="#fff"/></svg>
<div class="bottom-bar"></div>
<a class="to-top" href="#" aria-label="Back to top"><svg width="20" height="12" viewBox="0 0 20 12"><path d="M2 10l8-8 8 8" fill="none" stroke="#fff" stroke-width="2"/></svg></a>

</body>
</html>
```